Investment company needing business card

We are wanting a business card which looks sharp and easy on the eye. We are thinking of having a business card with the logo embossed on it, to really make it stand out. We will only have a small amount of information of the business card, person's name, position, email address and phone number

Contact Information for Business Card

Danielle Frost
Executive Assistant
+64 21 473 5162
danielf@harwickpartners.co.nz

Requirements
Must have
• Embossed logo
Should not have
• Not to be busy

```html
<!DOCTYPE html>
<html lang="en">
<head>
<meta charset="utf-8">
<title>Harwick Partners – Business Card</title>
<link rel="stylesheet" href="https://fonts.googleapis.com/css2?family=Open+Sans:wght@400;600;700&display=swap">
<style>
  :root {
    --backdrop: #2b2b2b;
    --card-white: #f4f4f4;
    --panel-grey: #666666;
    --band-grey: #5f5f5f;
    --text-white: #ffffff;
    --text-grey: #555555;
    --brand-green: #1fae6e;
  }
  * { box-sizing: border-box; margin: 0; padding: 0; }
  html, body {
    width: 1200px; height: 900px; overflow: hidden;
    background: var(--backdrop);
    font-family: "Open Sans", sans-serif;
  }
  .card {
    position: absolute;
    width: 700px; height: 400px;
    border-radius: 22px;
    background: var(--card-white);
    overflow: hidden;
    box-shadow: 0 12px 30px rgba(0,0,0,.45);
  }
  .card-front { left: 90px; top: 45px; }
  .card-back  { left: 410px; top: 465px; }

  /* front */
  .brand-area {
    position: absolute; left: 0; top: 0; width: 330px; height: 100%;
    display: flex; align-items: center; justify-content: center; gap: 12px;
  }
  .brand-mark { width: 22px; height: 22px; background: var(--brand-green); }
  .brand-name {
    font-weight: 700; font-size: 26px; letter-spacing: 1px;
    color: var(--text-grey); text-transform: uppercase; line-height: 1.05;
  }
  .contact-panel {
    position: absolute; left: 330px; top: 0; right: 0; height: 100%;
    background: var(--panel-grey);
    padding: 95px 30px 0 48px;
    color: var(--text-white);
  }
  .panel-notch {
    position: absolute; left: -14px; top: 88px;
    width: 0; height: 0;
    border-top: 18px solid transparent;
    border-bottom: 18px solid transparent;
    border-right: 14px solid var(--panel-grey);
  }
  .person-name { font-weight: 700; font-size: 21px; text-transform: uppercase; letter-spacing: .5px; }
  .person-role { font-size: 15px; margin-bottom: 18px; }
  .contact-list { list-style: none; font-size: 15px; }
  .contact-list li { display: flex; align-items: center; gap: 10px; margin-bottom: 4px; }
  .contact-list svg { width: 13px; height: 13px; fill: var(--text-white); flex: none; }
  .postal { margin-top: 18px; margin-left: 23px; font-size: 15px; line-height: 1.35; }

  /* back */
  .band { position: absolute; top: 0; height: 100%; background: var(--band-grey); }
  .band-left  { left: 50px;  width: 130px; }
  .band-right { left: 500px; width: 120px; }
  .back-brand {
    position: absolute; left: 180px; top: 0; width: 320px; height: 100%;
    display: flex; flex-direction: column; align-items: center; justify-content: center;
  }
  .back-brand .brand-row { display: flex; align-items: center; gap: 14px; margin-top: -30px; }
  .back-brand .brand-mark { width: 30px; height: 30px; }
  .back-brand .brand-name { font-size: 30px; }
  .web-address {
    position: absolute; bottom: 40px; left: 0; right: 0; text-align: center;
    font-size: 17px; letter-spacing: 1px; color: var(--text-grey);
  }
</style>
</head>
<body>
  <section class="card card-front">
    <div class="brand-area">
      <span class="brand-mark"></span>
      <span class="brand-name">Harwick<br>Partners</span>
    </div>
    <div class="contact-panel">
      <span class="panel-notch"></span>
      <p class="person-name">Danielle Frost</p>
      <p class="person-role">Executive Assistant</p>
      <ul class="contact-list">
        <li><svg viewBox="0 0 16 16"><path d="M3.6 1.2l2.4 2.4-1.4 2.2c.9 2 2.6 3.7 4.6 4.6l2.2-1.4 2.4 2.4-1.6 2.4C6.7 13.6 2.4 9.3 1.2 3.6z"/></svg>+64 21 473 5162</li>
        <li><svg viewBox="0 0 16 16"><path d="M1 3h14v10H1z M1.5 3.5 8 9l6.5-5.5" stroke="#666" stroke-width="1.2"/></svg>danielf@harwickpartners.co.nz</li>
        <li><svg viewBox="0 0 16 16"><circle cx="8" cy="8" r="7" fill="none" stroke="#fff" stroke-width="1.5"/><path d="M1 8h14M8 1c-3 3.5-3 10.5 0 14M8 1c3 3.5 3 10.5 0 14" fill="none" stroke="#fff" stroke-width="1.2"/></svg>www.harwickpartners.co.nz</li>
      </ul>
      <p class="postal">Po. box 201, Street Name,<br>City Name, Zip Code - 00000</p>
    </div>
  </section>

  <section class="card card-back">
    <span class="band band-left"></span>
    <span class="band band-right"></span>
    <div class="back-brand">
      <div class="brand-row">
        <span class="brand-mark"></span>
        <span class="brand-name">Harwick<br>Partners</span>
      </div>
    </div>
    <p class="web-address">www.harwickpartners.co.nz</p>
  </section>
</body>
</html>
```